Webpage/HTML page design for emailing to customers

I want to design a single webpage/HTML page that can be attached to an email for marketing purposes. I have attached our company logos, the main ones being VOLTRIDGE Generator and VOLTRIDGE Prime Power. I have attached a word document of the highlights I want to point out about us and our products. I have also attached some images to add to the page and a testimonial from one of our good trade customers. I am really looking for a page that instantly grabs the attention of the recipient.
Just confirming, this is for ONE page only. I am not looking for a website design.
The image attached of the 'Green' engine with features pointed out, I want to add to this a price and model reference. On or near the image I want the following -
- 44kW @ 2400rpm Rated Power - $4980 + GST Complete package displayed.

```html
<!DOCTYPE html>
<html lang="en">
<head>
<meta charset="utf-8">
<title>VOLTRIDGE Prime Power</title>
<link href="https://fonts.googleapis.com/css2?family=Open+Sans:wght@400;600;700&family=Roboto+Condensed:wght@400;700&display=swap" rel="stylesheet">
<style>
:root{
  --green:#3aa935;
  --blue:#2e3192;
  --blue-panel:rgba(38,44,150,.88);
  --ink:#2b2b2b;
  --muted:#777;
  --light:#f1f1f3;
  --line:#e2e2e2;
}
*{margin:0;padding:0;box-sizing:border-box}
html,body{width:681px;height:1200px;overflow:hidden;background:#fff}
body{font-family:"Open Sans",Arial,sans-serif;color:var(--ink);position:relative}
.heading{font-family:"Roboto Condensed",Arial,sans-serif;font-weight:700;text-transform:uppercase}

/* header */
.site-header{height:44px;display:flex;align-items:center;justify-content:space-between;padding:0 18px 0 16px}
.brand{display:flex;align-items:center;gap:6px;font-weight:700;color:var(--green);font-size:15px;letter-spacing:.2px}
.brand-mark{width:12px;height:12px;background:var(--green);border-radius:50%}
.main-nav{display:flex;align-items:center;gap:18px;font-size:8.5px;font-weight:600;color:#444}
.main-nav .active{color:var(--blue)}
.search-btn{width:16px;height:16px;border-radius:50%;background:var(--blue);display:flex;align-items:center;justify-content:center}

/* hero */
.hero{position:relative;height:311px}
.hero-photo{position:absolute;inset:0;background:linear-gradient(120deg,#9aa3ad 0%,#6c7178 30%,#b36a2a 55%,#8a4a1c 75%,#3c3f44 100%)}
.hero-panel{position:absolute;right:0;top:0;width:272px;height:100%;background:var(--blue-panel);padding:36px 22px 0 22px;color:#fff}
.hero-title{font-size:26px;line-height:1.05;letter-spacing:.5px;margin-bottom:14px}
.hero-text{font-size:8.6px;line-height:1.55;margin-bottom:10px}
.btn-green{display:inline-block;background:var(--green);color:#fff;font-size:9px;font-weight:700;padding:8px 20px;margin-top:6px}
.slider-dots{position:absolute;bottom:12px;left:50%;transform:translateX(-50%);display:flex;gap:5px}
.slider-dots span{width:6px;height:6px;border-radius:50%;background:#bbb}
.slider-dots span.on{background:#fff}

/* welcome */
.welcome{text-align:center;padding:24px 40px 0}
.section-title{font-size:15px;color:var(--green);letter-spacing:.4px}
.section-title .dark{color:var(--blue)}
.rule{width:40px;height:2px;background:var(--green);margin:6px auto 10px}
.welcome p{font-size:8.2px;line-height:1.6;color:var(--muted)}

/* highlights */
.highlights{display:flex;padding:30px 20px 0 24px;height:300px}
.hl-list{width:370px}
.block-title{font-size:15px;color:var(--ink);letter-spacing:.4px;margin-bottom:4px}
.block-title .accent{color:var(--green)}
.left-rule{width:30px;height:2px;background:var(--green);margin-bottom:14px}
.hl-list ul{list-style:none}
.hl-list li{font-size:8.4px;line-height:1.5;color:#444;padding-left:14px;position:relative;margin-bottom:11px}
.hl-list li::before{content:"";position:absolute;left:0;top:4px;width:6px;height:6px;background:var(--green)}
.more-link{font-size:8.4px;color:var(--blue);text-decoration:underline}
.hl-media{flex:1;margin-left:20px;display:flex;flex-direction:column;align-items:flex-end}
.hl-brand{font-size:12px;font-weight:700;color:var(--green);margin:4px 4px 6px 0}
.engine-figure{position:relative;width:236px;height:210px}
.engine-photo{position:absolute;inset:0;background:radial-gradient(ellipse at 50% 50%,#3f8f3a 0%,#2d6b2a 35%,#243026 62%,#e9ece9 88%,#fff 100%)}
.price-tag{position:absolute;right:0;bottom:0;background:var(--blue);color:#fff;padding:6px 9px;text-align:left;border-left:3px solid var(--green)}
.price-tag .model{font-size:8px;font-weight:600;line-height:1.3}
.price-tag .price{font-family:"Roboto Condensed",Arial,sans-serif;font-weight:700;font-size:15px;line-height:1.15;color:#fff}
.price-tag .pack{font-size:7px;color:#d6d8f2;line-height:1.3}

/* testimonial & news */
.two-col{display:flex;padding:16px 20px 0 24px;height:235px;gap:30px}
.col{flex:1}
.col-head{display:flex;align-items:center;justify-content:space-between}
.arrows{display:flex;gap:4px}
.arrows span{width:14px;height:14px;border-radius:50%;border:1px solid #bbb;font-size:9px;line-height:12px;text-align:center;color:#888}
.quote{font-size:8.2px;line-height:1.6;color:#555;margin-top:4px}
.person{display:flex;align-items:center;gap:10px;margin-top:14px}
.avatar{width:44px;height:44px;border-radius:50%;background:#c9c9cf}
.person-name{font-size:11px;font-weight:700}
.person-role{font-size:8px;color:var(--muted)}
.news-item{display:flex;gap:10px;margin-bottom:14px}
.news-thumb{width:78px;height:60px;flex:none;background:linear-gradient(135deg,#8d949c,#c47a34)}
.news-date{font-size:9px;font-weight:700;color:var(--ink)}
.news-tag{font-size:7.5px;color:var(--green);font-weight:600;margin:1px 0 3px}
.news-text{font-size:7.8px;line-height:1.5;color:#666}

/* partners */
.partners{background:var(--light);height:132px;text-align:center;padding:20px 30px 0}
.partners p{font-size:8.2px;color:var(--muted);margin-bottom:14px}
.partner-row{display:flex;justify-content:space-between;align-items:center;padding:0 10px}
.partner{display:flex;align-items:center;gap:5px;font-size:14px;font-weight:700;color:#9a9a9a}
.partner .dot{width:12px;height:12px;border-radius:50%;background:#9a9a9a}

/* footer */
.site-footer{position:absolute;left:0;right:0;bottom:0;height:78px;background:var(--blue);color:#fff;text-align:center;padding-top:13px}
.socials{display:flex;justify-content:center;gap:6px;margin-bottom:9px}
.socials span{width:15px;height:15px;border-radius:50%;background:#4a8ad8}
.foot-nav{display:flex;justify-content:center;gap:16px;font-size:8px;font-weight:600;margin-bottom:6px}
.copyright{font-size:7.5px;color:#c9cbe8}
</style>
</head>
<body>

<header class="site-header">
  <div class="brand"><span class="brand-mark"></span>VOLTRIDGE Prime Power</div>
  <nav class="main-nav">
    <span class="active">HOME</span><span>ABOUT US</span><span>OUR PRODUCTS</span><span>CLIENTS</span><span>CONTACT US</span>
    <span class="search-btn"><svg width="8" height="8" viewBox="0 0 8 8"><circle cx="3.3" cy="3.3" r="2.3" fill="none" stroke="#fff" stroke-width="1"/><line x1="5" y1="5" x2="7.3" y2="7.3" stroke="#fff" stroke-width="1"/></svg></span>
  </nav>
</header>

<section class="hero">
  <div class="hero-photo" role="img" aria-label="Diesel generator set on a workshop floor"></div>
  <div class="hero-panel">
    <h1 class="hero-title heading">VOLTRIDGE<br>Prime Power</h1>
    <p class="hero-text">Having distributed more than 750 diesel drivers across Australia since the start of 2011, of which there has been zero major failures, Keystone Pumps continues to support the sale of quality products available from Ardent Industries.</p>
    <p class="hero-text">This leads to the supply of low cost, heavy duty diesel engines being operated at what would appear to be excessive RPM.</p>
    <span class="btn-green">LEARN MORE</span>
  </div>
  <div class="slider-dots"><span class="on"></span><span></span><span></span></div>
</section>

<section class="welcome">
  <h2 class="section-title heading">Welcome to our <span class="dark">VOLTRIDGE</span> Prime Power</h2>
  <div class="rule"></div>
  <p>Lorem ipsum dolor sit amet, consectetur adipiscing elit, sed do eiusmod tempor incididunt ut labore et dolore magna aliqua. Ut enim ad minim veniam, quis nostrud exercitation ullamco laboris nisi ut aliquip ex ea commodo consequat. Duis aute irure dolor in reprehenderit in voluptate velit esse cillum dolore eu fugiat nulla pariatur. Excepteur sint occaecat cupidatat non proident, sunt in culpa qui officia deserunt mollit anim id est laborum.</p>
</section>

<section class="highlights">
  <div class="hl-list">
    <h2 class="block-title heading">Our <span class="accent">Highlights</span></h2>
    <div class="left-rule"></div>
    <ul>
      <li>The Proven Alternative</li>
      <li>Celebrating 10 Years of VOLTRIDGE in Australia – 2006/2016</li>
      <li>VOLTRIDGE is the READY option. Purpose build industrial diesel engine power packs that tick all the right boxes. Simple in Operation, Rugged in Construction, Unbreakable in Function.</li>
      <li>VOLTRIDGE industrial diesel engines are located across the country. From Darwin to Hobart, Perth to Sydney.</li>
      <li>VOLTRIDGE are VALUE PACKED. Supplied complete from Radiator to Flywheel including the widely acclaimed Engine/Guard control panel.</li>
    </ul>
    <span class="more-link">Click here to read all our highlights &gt;&gt;</span>
  </div>
  <div class="hl-media">
    <div class="hl-brand">VOLTRIDGE Generator</div>
    <div class="engine-figure">
      <div class="engine-photo" role="img" aria-label="Green industrial diesel engine with labelled features"></div>
      <div class="price-tag">
        <div class="model">44kW @ 2400rpm Rated Power</div>
        <div class="price">$4980 + GST</div>
        <div class="pack">Complete package displayed</div>
      </div>
    </div>
  </div>
</section>

<section class="two-col">
  <div class="col">
    <div class="col-head">
      <h2 class="block-title heading">What our <span class="accent">client say</span></h2>
      <div class="arrows"><span>‹</span><span>›</span></div>
    </div>
    <div class="left-rule"></div>
    <p class="quote">"In times where suppliers to the new construction industry are fiercely competing for every new opportunity it often becomes a race to the bottom, and the cheapest offer usually wins the order. In the diesel drive pump industry that leads to the supply of low cost, lower quality diesel engines being operated at what would appear to be excessive RPM. The end result is always problematic and shorter lifetimes of the return scarcely do not pay..."</p>
    <div class="person">
      <div class="avatar" role="img" aria-label="Portrait of the client"></div>
      <div>
        <div class="person-name heading">Alan Reeves</div>
        <div class="person-role">Manager, place of working</div>
      </div>
    </div>
  </div>
  <div class="col">
    <h2 class="block-title heading">Latest <span class="accent">News</span></h2>
    <div class="left-rule"></div>
    <div class="news-item">
      <div class="news-thumb" role="img" aria-label="Generator on site"></div>
      <div>
        <div class="news-date heading">September 5, 2015</div>
        <div class="news-tag">BEST OF VOLTRIDGE BLOGS</div>
        <p class="news-text">New engine packs now ship with an upgraded control panel and a longer service interval for remote sites.</p>
      </div>
    </div>
    <div class="news-item">
      <div class="news-thumb" role="img" aria-label="Engine being serviced"></div>
      <div>
        <div class="news-date heading">September 5, 2015</div>
        <div class="news-tag">BEST OF VOLTRIDGE BLOGS</div>
        <p class="news-text">Our dealer network grows again with new service partners opening in Darwin, Hobart and Perth.</p>
      </div>
    </div>
  </div>
</section>

<section class="partners">
  <h2 class="section-title heading">Our <span class="dark">Partners</span></h2>
  <div class="rule"></div>
  <p>Lorem ipsum dolor sit amet, consectetur adipiscing elit, sed do eiusmod tempor incididunt ut labore et dolore magna aliqua.</p>
  <div class="partner-row">
    <span class="partner"><span class="dot"></span>Tunewave</span>
    <span class="partner">Corelight</span>
    <span class="partner">Snapfold</span>
    <span class="partner">framevault</span>
    <span class="partner"><span class="dot"></span>Tallybox</span>
    <span class="partner">Snapfold</span>
  </div>
</section>

<footer class="site-footer">
  <div class="socials"><span></span><span></span><span></span><span></span><span></span></div>
  <nav class="foot-nav"><span>HOME</span><span>ABOUT US</span><span>OUR PRODUCTS</span><span>CLIENTS</span><span>CONTACT US</span></nav>
  <div class="copyright">Copyright © 2015 VOLTRIDGE. All rights reserved.</div>
</footer>

</body>
</html>
```